Desktop and Networking Support Course 9.17.25

Important the ad should not be very busy with the text taking up the major part of the ad .. please do not make the text so big that it takes up most of the ad..
Flyer Design Brief for Graphic Artist
also i am looking for something unique or creative that it will stand out .
Size & Layout:
Full Page with Bleed: 8” x 10.75” + 0.25” bleed on all sides.
Footer Space: Leave a 1-inch margin at the bottom for footer content (e.g., contact info, logo, or call-to-action).
Target Audience:
College-age students (around 24 years old)
Located in the USA
Interested in creative, professional, and career-building opportunities
Purpose:
To attract students to enroll in a college program
Flyer should be eye-catching, unique, and creative
Text must be clear and readable,
Design Style:
Use vector art, typography, or photography — your choice
If using photography, feature a white young professional USA citizen:
Wearing a white collared shirt
not with long hair
Creative Direction:
The flyer should stand out visually — something people would want to look at and keep
Showcase creativity and professionalism
Use bold colors, dynamic layout, or unexpected design elements to grab attention
Avoid clutter — keep the design balanced and clean
Text Suggestions (can be adjusted):
Footer,
please leave one inch on the bottom for the footer

```html
<!DOCTYPE html>
<html lang="en">
<head>
<meta charset="utf-8">
<title>Desktop &amp; Network Support Course Flyer</title>
<link rel="stylesheet" href="https://fonts.googleapis.com/css2?family=Playfair+Display:wght@700;800&family=Lexend:wght@400;500;700&family=Inter:wght@400;500&display=swap">
<style>
  :root {
    --bg: #e6e7ea;
    --orange: #f7892a;
    --orange-text: #ff8a1f;
    --teal: #032b33;
    --shade: #061a1f;
    --white: #ffffff;
    --ink: #1d2327;
    --footer: #d4d5d9;
    --divider-blue: #1f78c1;
  }
  * { margin: 0; padding: 0; box-sizing: border-box; }
  html, body { width: 1200px; height: 2616px; overflow: hidden; background: var(--bg); }
  .flyer {
    position: absolute; left: 60px; top: 583px;
    width: 948px; height: 1274px;
    transform: scale(1.13924); transform-origin: top left;
    overflow: hidden; background: var(--footer);
    box-shadow: 0 10px 30px rgba(0,0,0,.15);
    font-family: "Inter", sans-serif;
  }
  .photo {
    position: absolute; left: 0; top: 0; width: 948px; height: 1159px;
    background:
      radial-gradient(ellipse 260px 360px at 640px 560px, #d8cfc6 0%, rgba(216,207,198,0) 70%),
      linear-gradient(100deg, #4d6668 0%, #b9c6c4 40%, #e9ecea 60%, #9fb2b1 85%, #7d9393 100%);
  }
  .shapes { position: absolute; left: 0; top: 0; width: 948px; height: 1159px; }
  .footer-space { position: absolute; left: 0; top: 1159px; width: 948px; height: 115px; background: var(--footer); }
  .headline {
    position: absolute; left: 55px; top: 36px;
    font-family: "Playfair Display", serif; font-weight: 800;
    font-size: 61px; line-height: 66px; color: var(--white); letter-spacing: -0.5px;
  }
  .course {
    position: absolute; left: 58px; top: 192px;
    font-family: "Lexend", sans-serif; font-size: 29px; line-height: 40px; color: var(--white);
  }
  .stat { position: absolute; left: 42px; top: 520px; font-family: "Lexend", sans-serif; }
  .stat-figure { font-size: 52px; font-weight: 700; color: var(--orange-text); line-height: 60px; }
  .stat-label { font-size: 31px; line-height: 45px; color: var(--white); }
  .stat-year { font-size: 31px; line-height: 45px; color: var(--orange-text); }
  .title {
    position: absolute; left: 42px; top: 702px;
    font-family: "Lexend", sans-serif; font-size: 53px; line-height: 57px; color: var(--white);
  }
  .title .accent { color: var(--orange-text); }
  .jobs {
    position: absolute; left: 42px; top: 866px;
    font-family: "Inter", sans-serif; font-size: 26px; line-height: 36px; color: var(--white);
  }
  .jobs .accent { color: var(--orange-text); }
  .perk { position: absolute; font-size: 23px; line-height: 29px; color: var(--white); }
  .perk svg { display: block; margin-bottom: 14px; }
  .perk-format { left: 384px; top: 993px; }
  .perk-aid { left: 616px; top: 993px; }
  .perk-divider { position: absolute; left: 571px; top: 1010px; width: 2px; height: 110px; background: var(--divider-blue); }
  .features { position: absolute; left: 697px; top: 565px; width: 236px; text-align: center; color: var(--ink); }
  .feature { padding: 12px 0 18px; font-size: 21px; line-height: 24px; }
  .feature + .feature { border-top: 2px solid var(--orange); }
  .feature svg { display: block; margin: 0 auto 10px; }
</style>
</head>
<body>
  <div class="flyer">
    <div class="photo" role="img" aria-label="Photo of a smiling young professional in a white collared shirt standing in a bright office"></div>

    <svg class="shapes" viewBox="0 0 948 1159" aria-hidden="true">
      <defs>
        <linearGradient id="shadeFade" x1="0" y1="0" x2="0.4" y2="1">
          <stop offset="0" stop-color="#06222a" stop-opacity="0.8"/>
          <stop offset="1" stop-color="#020607" stop-opacity="0.97"/>
        </linearGradient>
      </defs>
      <polygon points="0,247 192,422 567,782 217,1159 0,1159" fill="url(#shadeFade)"/>
      <polygon points="0,0 747,0 192,422 0,247" fill="var(--orange)" opacity="0.95"/>
      <polygon points="948,377 567,782 948,1159" fill="var(--white)"/>
      <polygon points="567,782 948,1159 217,1159" fill="var(--teal)"/>
    </svg>

    <div class="footer-space"></div>

    <h1 class="headline">Your Career Is Just<br>a Click Away</h1>
    <p class="course">Desktop &amp; Network<br>Support Course</p>

    <div class="stat">
      <div class="stat-figure">90%</div>
      <div class="stat-label">Employment Rate –</div>
      <div class="stat-year">Class of 2024</div>
    </div>

    <h2 class="title"><span class="accent">Master Desktop</span><br>Operating Systems</h2>

    <p class="jobs">Prepare for 3 of the<br>Top 10 Tech Jobs <span class="accent">National Career<br>Review 2025</span></p>

    <div class="perk perk-format">
      <svg width="44" height="48" viewBox="0 0 44 48" fill="none" stroke="#fff" stroke-width="2">
        <circle cx="22" cy="12" r="8"/>
        <path d="M8 44 C8 30 14 25 22 25 C30 25 36 30 36 44"/>
        <rect x="12" y="32" width="20" height="12" rx="1"/>
        <path d="M4 45 H40"/>
      </svg>
      In-Person and<br>Remote Options
    </div>
    <div class="perk-divider"></div>
    <div class="perk perk-aid">
      <svg width="48" height="44" viewBox="0 0 48 44" fill="none" stroke="#fff" stroke-width="2">
        <path d="M4 14 L24 5 L44 14 L24 23 Z"/>
        <path d="M12 18 V28 C12 32 36 32 36 28 V18"/>
        <path d="M44 14 V26"/>
        <rect x="4" y="32" width="18" height="9" rx="1"/>
      </svg>
      Partial Scholarships<br>Offered
    </div>

    <div class="features">
      <div class="feature">
        <svg width="50" height="50" viewBox="0 0 50 50" fill="none" stroke="var(--ink)" stroke-width="2">
          <circle cx="10" cy="10" r="4"/><circle cx="40" cy="10" r="4"/>
          <circle cx="10" cy="40" r="4"/><circle cx="40" cy="40" r="4"/>
          <circle cx="25" cy="25" r="5"/><circle cx="25" cy="5" r="3"/><circle cx="25" cy="45" r="3"/>
          <path d="M13 13 L21 21 M37 13 L29 21 M13 37 L21 29 M37 37 L29 29 M14 10 H36 M14 40 H36 M25 8 V20 M25 30 V42"/>
        </svg>
        Hands-On Desktop &amp;<br>Network Training
      </div>
      <div class="feature">
        <svg width="52" height="52" viewBox="0 0 52 52" fill="none" stroke="var(--ink)" stroke-width="2">
          <circle cx="26" cy="26" r="15"/>
          <ellipse cx="26" cy="26" rx="7" ry="15"/>
          <path d="M11 26 H41 M14 18 H38 M14 34 H38"/>
          <circle cx="26" cy="4" r="3"/><circle cx="26" cy="48" r="3"/>
          <circle cx="4" cy="26" r="3"/><circle cx="48" cy="26" r="3"/>
          <circle cx="9" cy="9" r="3"/><circle cx="43" cy="43" r="3"/>
        </svg>
        Real-World<br>Troubleshooting Skills
      </div>
      <div class="feature">
        <svg width="48" height="50" viewBox="0 0 48 50" fill="none" stroke="var(--ink)" stroke-width="2">
          <path d="M10 30 C8 14 14 4 24 4 C34 4 40 14 38 30"/>
          <circle cx="24" cy="17" r="7"/>
          <rect x="10" y="30" width="28" height="16" rx="1"/>
          <circle cx="24" cy="38" r="2"/>
          <path d="M4 47 H44"/>
        </svg>
        Ready for IT Jobs
      </div>
    </div>
  </div>
</body>
</html>
```